Business Cards for a law firm

Business cards for our law firm. Use our silhoette logo and OAK PARTNERS - check our website (www.oakpartners.example)

Contact Information for Business Card

our silhouette logo, OAK PARTNERS, 800-555-0147, Dorian Pemberton, dorian@oakpartners.example

Requirements
Must have
• our silhouette logo, OAK PARTNERS, 800-555-0147, Dorian Pemberton, dorian@oakpartners.example

```html
<!DOCTYPE html>
<html lang="en">
<head>
<meta charset="utf-8">
<title>Oak Partners — Business Cards</title>
<link rel="stylesheet" href="https://fonts.googleapis.com/css2?family=Montserrat:wght@400;600;700&display=swap">
<style>
  :root {
    --backdrop: #e6e7ea;
    --navy: #2b3578;
    --navy-deep: #232c66;
    --navy-mid: #34439a;
    --navy-soft: #4a5bb3;
    --paper: #ffffff;
    --ink-grey: #4a4d57;
  }
  * { box-sizing: border-box; margin: 0; padding: 0; }
  html, body {
    width: 1200px; height: 913px; overflow: hidden;
    background: var(--backdrop);
    font-family: "Montserrat", sans-serif;
  }
  .sheet {
    position: relative; width: 1200px; height: 913px;
    display: flex; flex-direction: column; align-items: center; justify-content: center; gap: 40px;
  }
  .card {
    position: relative; width: 580px; height: 332px;
    border-radius: 22px; overflow: hidden;
    box-shadow: 0 10px 28px rgba(20, 24, 50, 0.22);
  }
  /* Back side */
  .card--back { background: var(--navy-mid); }
  .card__pattern {
    position: absolute; inset: 0;
    background: linear-gradient(120deg, var(--navy-deep) 0%, var(--navy-mid) 55%, var(--navy-soft) 100%);
  }
  .card__brand {
    position: absolute; left: 300px; top: 150px;
    display: flex; align-items: center; gap: 12px;
    color: var(--paper);
  }
  .brand-dot { width: 14px; height: 14px; border-radius: 50%; background: var(--paper); }
  .brand-name {
    font-weight: 600; font-size: 22px; letter-spacing: 3px; text-transform: uppercase;
  }
  /* Front side */
  .card--front { background: var(--paper); }
  .card__artwork {
    position: absolute; right: 0; top: 0; width: 240px; height: 100%;
    background: linear-gradient(180deg, rgba(43,53,120,0.10) 0%, rgba(43,53,120,0.28) 100%);
  }
  .front__title {
    position: absolute; left: 40px; top: 60px;
    color: var(--navy); font-weight: 700; font-size: 30px; letter-spacing: 4px;
  }
  .front__name {
    position: absolute; left: 40px; top: 140px;
    color: var(--navy); font-weight: 700; font-size: 19px; letter-spacing: 1px;
  }
  .contact-list {
    position: absolute; left: 40px; bottom: 36px;
    list-style: none; display: flex; flex-direction: column; gap: 10px;
  }
  .contact-item {
    display: flex; align-items: center; gap: 12px;
    color: var(--ink-grey); font-size: 15px; font-weight: 400; letter-spacing: 0.3px;
  }
  .contact-icon { width: 16px; height: 16px; flex: none; }
</style>
</head>
<body>
<main class="sheet">

  <section class="card card--back" aria-label="Card back">
    <div class="card__pattern" role="img" aria-label="Repeating brand pattern in shades of navy"></div>
    <div class="card__brand">
      <span class="brand-dot"></span>
      <span class="brand-name">Oak Partners</span>
    </div>
  </section>

  <section class="card card--front" aria-label="Card front">
    <div class="card__artwork" role="img" aria-label="Large navy brand artwork"></div>
    <h1 class="front__title">OAK PARTNERS</h1>
    <h2 class="front__name">DORIAN PEMBERTON</h2>
    <ul class="contact-list">
      <li class="contact-item">
        <svg class="contact-icon" viewBox="0 0 16 16"><path fill="#2b3578" d="M3.5 1.5l2.5 2.6-1.3 1.9c.8 1.8 2.2 3.2 4 4l1.9-1.3 2.6 2.5-1.6 2.2C6.8 13.3 2.7 9.2 1.4 3.1z"/></svg>
        <span>800-555-0147</span>
      </li>
      <li class="contact-item">
        <svg class="contact-icon" viewBox="0 0 16 16"><rect x="1" y="3" width="14" height="10" rx="1" fill="#2b3578"/><path d="M1.5 3.8L8 9l6.5-5.2" stroke="#fff" stroke-width="1.2" fill="none"/></svg>
        <span>dorian@oakpartners.example</span>
      </li>
      <li class="contact-item">
        <svg class="contact-icon" viewBox="0 0 16 16"><circle cx="8" cy="8" r="7" fill="#2b3578"/><path d="M1 8h14M8 1c-2.5 2-2.5 12 0 14M8 1c2.5 2 2.5 12 0 14" stroke="#fff" stroke-width="1" fill="none"/></svg>
        <span>www.oakpartners.example</span>
      </li>
    </ul>
  </section>

</main>
</body>
</html>
```